Makers' Hollow - Landing page for small and large screen

Makers’ Hollow gives you the space you need to take your side project from idea to reality.

With three days of focused work, it’s a place for you iron out the details of your business idea away from the distractions of the city.

The full copy and structure is here:
https://www.makershollow.co.uk/landing

What it needs, a touch of colour.

Target Market(s)

25-35 working in digital industry, software developer, a UI or UX designer

Number of Pages Required

1 page

Font styles to use
Sans Serif

Colors
0292cd
33b8a4
86cfc6
fdf9cf
ec1f27

Requirements
Should not have
• gradients or too much images

```html
<!DOCTYPE html>
<html lang="en">
<head>
<meta charset="utf-8">
<title>Makers' Hollow – Landing</title>
<link rel="stylesheet" href="https://fonts.googleapis.com/css2?family=Open+Sans:ital,wght@0,400;0,600;0,700;1,600&family=Raleway:wght@600;700;800&display=swap">
<style>
:root{
  --ink:#1c1c1c;
  --body:#555a5f;
  --muted:#8a8f94;
  --red:#e3202a;
  --blue:#0f74c2;
  --link-blue:#0a83c6;
  --pale:#eaf3f7;
  --line:#c9cdd1;
  --white:#ffffff;
  --hero-dark:#23262a;
}
*{margin:0;padding:0;box-sizing:border-box}
html,body{width:1200px;height:3782px;overflow:hidden;background:var(--white)}
body{position:relative;font-family:'Open Sans',sans-serif;color:var(--body)}
.abs{position:absolute}
.head{font-family:'Raleway',sans-serif;color:var(--ink);font-weight:700}

/* hero */
.hero{left:0;top:0;width:1200px;height:668px;background:linear-gradient(90deg,#2a2d31 0%,#3b3f44 45%,#6e6a66 70%,#4a4b4e 100%)}
.brand{left:111px;top:40px;font-family:'Raleway',sans-serif;font-weight:700;font-size:36px;color:var(--white)}
.tagline{left:111px;top:90px;font-size:21px;color:var(--white);letter-spacing:.5px}
.nav{left:592px;top:70px;display:flex;gap:34px;font-size:16px;font-weight:600;color:var(--white)}
.nav .active{color:var(--red)}
.hero-title{left:111px;top:192px;font-family:'Raleway',sans-serif;font-weight:800;font-size:72px;line-height:92px;color:var(--white);letter-spacing:1px}
.btn-ghost{border:2px solid var(--white);border-radius:30px;color:var(--white);font-weight:700;font-size:16px;display:flex;align-items:center;justify-content:center;letter-spacing:.5px}
.btn-red{border:2px solid var(--red);border-radius:30px;color:var(--red);font-weight:700;font-size:15px;display:flex;align-items:center;justify-content:center;letter-spacing:.5px;background:var(--white)}

/* welcome */
.welcome-title{left:111px;top:770px;font-size:44px;line-height:61px;font-weight:700}
.lead{left:111px;top:900px;width:470px;font-style:italic;font-weight:600;font-size:17px;line-height:34px;color:var(--link-blue)}
.copy{font-size:14.5px;line-height:25px;color:var(--body)}
.feature{left:690px;display:flex;gap:30px;align-items:flex-start}
.feature h3{font-family:'Raleway',sans-serif;font-size:34px;color:var(--ink);font-weight:700}
.feature p{font-size:13.5px;color:var(--body);margin-top:12px}

/* join */
.join{left:0;top:1374px;width:1200px;height:624px;background:var(--pale)}
.join-photo{left:0;top:1374px;width:643px;height:624px;background:linear-gradient(120deg,#f4f4f2,#e6e6e4 60%,#d9d9d8)}
.join-title{left:650px;top:1442px;font-size:40px;line-height:62px}
.perks{left:650px;top:1592px;list-style:none;font-size:14.5px;color:var(--body)}
.perks li{display:flex;align-items:center;gap:14px;height:33.6px}

/* organisers */
.section-title{left:0;width:1200px;text-align:center;font-size:40px}
.avatar{left:514px;top:2190px;width:172px;height:172px;border-radius:50%;background:radial-gradient(circle,#5a5652,#2e2c2b);border:6px solid #f2f2f2;box-shadow:0 2px 10px rgba(0,0,0,.15)}
.name{left:0;width:1200px;text-align:center;top:2388px;font-size:29px;font-weight:600}
.bio{left:220px;width:760px;top:2446px;text-align:center;font-size:14.5px;line-height:32px;color:var(--body)}
.social{display:flex;gap:8px}
.social span{width:52px;height:52px;border-radius:50%;border:1.5px solid #bbbfc3;display:flex;align-items:center;justify-content:center}
.social span i{width:12px;height:12px;border-radius:50%;background:var(--blue)}

/* feedback */
.feedback{left:0;top:2737px;width:1200px;height:333px;background:var(--blue)}
.feedback-title{left:0;width:1200px;top:2800px;text-align:center;color:var(--white);font-size:42px}
.feedback-copy{left:0;width:1200px;top:2874px;text-align:center;color:var(--white);font-size:15.5px}

/* contact */
.col-head{font-family:'Raleway',sans-serif;font-weight:700;font-size:22px;color:var(--ink)}
.field{border:1.5px solid #b6babe;border-radius:6px;font-size:13px;color:#444;padding:12px 16px}
.submit{left:617px;top:3584px;width:96px;height:40px;border-radius:22px;background:var(--red);color:var(--white);font-weight:700;font-size:13px;display:flex;align-items:center;justify-content:center}
.info{left:776px;display:flex;gap:22px;font-size:13.5px;color:#444;line-height:24px}
.ring{width:36px;height:36px;border-radius:50%;border:1.5px solid #c7cbcf;display:flex;align-items:center;justify-content:center;flex:none}
.ring i{width:10px;height:10px;border-radius:50%;background:var(--red)}
.footer-line{left:111px;top:3674px;width:968px;height:1px;background:#d7dadd}
.copyright{left:0;width:1200px;top:3712px;text-align:center;font-size:13.5px;color:#555}
</style>
</head>
<body>

<!-- Hero -->
<div class="abs hero" role="img" aria-label="Photo of a smiling woman in a light blazer at a laptop in a bright office, blurred background"></div>
<div class="abs brand">Makers' Hollow</div>
<div class="abs tagline">create. connect. collaborate</div>
<nav class="abs nav"><span class="active">Home</span><span>About us</span><span>Services</span><span>Blog</span><span>Contact us</span>
  <svg width="16" height="16" viewBox="0 0 16 16" style="margin-top:3px"><circle cx="6.5" cy="6.5" r="5" fill="none" stroke="#fff" stroke-width="2.2"/><line x1="10.3" y1="10.3" x2="15" y2="15" stroke="#fff" stroke-width="2.5"/></svg>
</nav>
<h1 class="abs hero-title">CREATE.<br>CONNECT.<br>COLLABORATE.</h1>
<div class="abs btn-ghost" style="left:116px;top:494px;width:204px;height:58px">GET MORE INFO</div>
<svg class="abs" style="left:42px;top:312px" width="24" height="36" viewBox="0 0 24 36"><polyline points="20,3 5,18 20,33" fill="none" stroke="#fff" stroke-width="4"/></svg>
<svg class="abs" style="left:1134px;top:312px" width="24" height="36" viewBox="0 0 24 36"><polyline points="4,3 19,18 4,33" fill="none" stroke="#fff" stroke-width="4"/></svg>

<!-- Welcome -->
<h2 class="abs head welcome-title">WELCOME TO<br>MAKERS' HOLLOW</h2>
<p class="abs lead">Makers’ Hollow gives you the space you need to take your side project from idea to reality.</p>
<p class="abs copy" style="left:111px;top:1000px;width:470px">Calling all creatives! Whether you’re a software developer, a UI or UX designer, a product creator or an artworker, you’ll know only too well that great work rarely materialises when you’re in the wrong environment.</p>
<p class="abs copy" style="left:111px;top:1122px;width:470px">Phones buzzing. Emails pinging. Huddle calls incoming… distractions are everywhere – and they do nothing for your motivation.</p>
<div class="abs btn-red" style="left:111px;top:1215px;width:154px;height:46px">READ MORE</div>

<div class="abs feature" style="top:810px">
  <svg width="64" height="60" viewBox="0 0 64 60"><rect x="4" y="12" width="40" height="40" rx="4" fill="none" stroke="#0a83c6" stroke-width="4"/><path d="M22 38 L48 10 L56 18 L30 44 L20 46 Z" fill="#0a83c6"/></svg>
  <div><h3>CREATE</h3><p>Nam libero tempore, cum soluta nobis est elige</p></div>
</div>
<div class="abs feature" style="top:956px">
  <svg width="64" height="60" viewBox="0 0 64 60"><rect x="6" y="8" width="26" height="16" rx="8" transform="rotate(40 19 16)" fill="none" stroke="#0a83c6" stroke-width="5"/><rect x="26" y="34" width="26" height="16" rx="8" transform="rotate(40 39 42)" fill="none" stroke="#0a83c6" stroke-width="5"/><line x1="24" y1="24" x2="36" y2="36" stroke="#0a83c6" stroke-width="5"/></svg>
  <div><h3>CONNECT</h3><p>Nam libero tempore, cum soluta nobis est elige</p></div>
</div>
<div class="abs feature" style="top:1102px">
  <svg width="64" height="70" viewBox="0 0 64 70"><circle cx="32" cy="26" r="22" fill="#0a83c6"/><rect x="22" y="44" width="20" height="14" fill="#0a83c6"/><rect x="24" y="60" width="16" height="5" rx="2" fill="#0a83c6"/><circle cx="32" cy="26" r="7" fill="#fff"/></svg>
  <div><h3>COLLABORATE</h3><p>Nam libero tempore, cum soluta nobis est elige</p></div>
</div>

<!-- Join -->
<div class="abs join"></div>
<div class="abs join-photo" role="img" aria-label="Top-down photo of hands typing on a laptop beside a tablet, glasses, coffee cup, apple and phone on a white desk"></div>
<h2 class="abs head join-title">JOIN THE RETREAT<br>AND ENJOY</h2>
<ul class="abs perks">
  <li><svg width="16" height="16" viewBox="0 0 16 16"><circle cx="8" cy="8" r="8" fill="#0a83c6"/><polyline points="4,8 7,11 12,5" fill="none" stroke="#fff" stroke-width="2"/></svg>Three, full days of distraction-free work</li>
  <li><svg width="16" height="16" viewBox="0 0 16 16"><circle cx="8" cy="8" r="8" fill="#0a83c6"/><polyline points="4,8 7,11 12,5" fill="none" stroke="#fff" stroke-width="2"/></svg>A chance to hone your side project away from the office</li>
  <li><svg width="16" height="16" viewBox="0 0 16 16"><circle cx="8" cy="8" r="8" fill="#0a83c6"/><polyline points="4,8 7,11 12,5" fill="none" stroke="#fff" stroke-width="2"/></svg>The opportunity to collaborate with likeminded creatives</li>
  <li><svg width="16" height="16" viewBox="0 0 16 16"><circle cx="8" cy="8" r="8" fill="#0a83c6"/><polyline points="4,8 7,11 12,5" fill="none" stroke="#fff" stroke-width="2"/></svg>Good, honest feedback and insight from fellow attendees</li>
  <li><svg width="16" height="16" viewBox="0 0 16 16"><circle cx="8" cy="8" r="8" fill="#0a83c6"/><polyline points="4,8 7,11 12,5" fill="none" stroke="#fff" stroke-width="2"/></svg>Daily yoga and meditation to help fuel your ideas</li>
  <li><svg width="16" height="16" viewBox="0 0 16 16"><circle cx="8" cy="8" r="8" fill="#0a83c6"/><polyline points="4,8 7,11 12,5" fill="none" stroke="#fff" stroke-width="2"/></svg>Three, nutritious and delicious meals a day</li>
  <li><svg width="16" height="16" viewBox="0 0 16 16"><circle cx="8" cy="8" r="8" fill="#0a83c6"/><polyline points="4,8 7,11 12,5" fill="none" stroke="#fff" stroke-width="2"/></svg>Healthy, low-sugar snacks to get you through the day</li>
</ul>
<div class="abs btn-red" style="left:650px;top:1865px;width:152px;height:50px">JOIN US NOW!</div>

<!-- Organisers -->
<h2 class="abs head section-title" style="top:2096px">MEET YOUR RETREAT ORGANISERS</h2>
<div class="abs avatar" role="img" aria-label="Portrait photo of organiser Tomas Varga"></div>
<div class="abs head name">Tomas Varga</div>
<p class="abs bio">A software engineer in London, Tomas knows only too well the challenges faced by creatives; it’s the reason he’s organised the Makers’ Hollow, to give everyone the space and time to do their best work. Armed with his trusty camera, photographer Tomas is also a biohacker enthusiast and a thoroughly good egg.</p>
<div class="abs social" style="left:514px;top:2570px"><span><i></i></span><span><i></i></span><span><i></i></span></div>
<svg class="abs" style="left:102px;top:2480px" width="18" height="30" viewBox="0 0 18 30"><polyline points="15,3 4,15 15,27" fill="none" stroke="#999" stroke-width="3"/></svg>
<svg class="abs" style="left:1078px;top:2480px" width="18" height="30" viewBox="0 0 18 30"><polyline points="3,3 14,15 3,27" fill="none" stroke="#999" stroke-width="3"/></svg>

<!-- Feedback -->
<div class="abs feedback"></div>
<h2 class="abs head feedback-title">WHAT DO YOU THINK?</h2>
<p class="abs feedback-copy">Sound good? Keen to know more? Share some feedback via the button below and we can hone the Retreat to suit you.</p>
<div class="abs btn-ghost" style="left:476px;top:2928px;width:250px;height:66px">SHARE YOUR THOUGHTS</div>

<!-- Contact -->
<h2 class="abs head section-title" style="top:3170px">CONTACT US</h2>
<div class="abs col-head" style="left:111px;top:3298px">Contact form</div>
<div class="abs field" style="left:111px;top:3357px;width:297px;height:48px">Name :</div>
<div class="abs field" style="left:418px;top:3357px;width:295px;height:48px">Phone no :</div>
<div class="abs field" style="left:111px;top:3420px;width:602px;height:46px">Email :</div>
<div class="abs field" style="left:111px;top:3480px;width:602px;height:86px">Message :</div>
<div class="abs submit">SUBMIT</div>

<div class="abs col-head" style="left:776px;top:3300px">Contact Information</div>
<div class="abs info" style="top:3356px">
  <span class="ring"><svg width="14" height="18" viewBox="0 0 14 18"><path d="M7 0C3 0 0 3 0 7c0 5 7 11 7 11s7-6 7-11c0-4-3-7-7-7z" fill="#e3202a"/><circle cx="7" cy="7" r="2.5" fill="#fff"/></svg></span>
  <span>North Quay<br>Harbourton</span>
</div>
<div class="abs info" style="top:3410px">
  <span class="ring"><svg width="16" height="16" viewBox="0 0 16 16"><path d="M3 1l3 3-2 2c1 2 3 4 5 5l2-2 3 3-2 3C6 15 1 10 0 4z" fill="#e3202a"/></svg></span>
  <span style="line-height:36px">+1 555 010 2040</span>
</div>
<div class="abs info" style="top:3460px">
  <span class="ring"><svg width="16" height="12" viewBox="0 0 16 12"><rect width="16" height="12" rx="1" fill="#e3202a"/><polyline points="1,1 8,7 15,1" fill="none" stroke="#fff" stroke-width="1.5"/></svg></span>
  <span style="line-height:36px">info@makershollow.co.uk</span>
</div>
<div class="abs col-head" style="left:776px;top:3522px">Social Media</div>
<div class="abs" style="left:774px;top:3562px;display:flex;gap:10px">
  <span class="ring"><i></i></span><span class="ring"><i></i></span><span class="ring"><i></i></span>
</div>

<div class="abs footer-line"></div>
<p class="abs copyright">Copyright © 2019, Makers’ Hollow. All rights reserved.</p>
<svg class="abs" style="left:1060px;top:3704px" width="30" height="18" viewBox="0 0 30 18"><polyline points="3,15 15,4 27,15" fill="none" stroke="#b5b9bd" stroke-width="3"/></svg>

</body>
</html>
```